Local fast-growing company in the service sector

We are looking for a modern business card design, which should also appear on our letterheads

Target Market(s)

Private and industrial sectors

Contact Information for Business Card

Vorname Name
Kellberger Str. 18
73418 Rettenau
Tel.: 07146-839214-0
Name@agentur-kvtl.de

Colors
9d9d9d
919191
aaaaaa

Requirements
Must have
• The logo (file) in silver

```html
<!DOCTYPE html>
<html lang="de">
<head>
<meta charset="utf-8">
<title>KVTL – Visitenkarte</title>
<link rel="stylesheet" href="https://fonts.googleapis.com/css2?family=Saira:wght@600;700&family=Didact+Gothic&display=swap">
<style>
  :root {
    --page: #e6e6e6;
    --card-dark: #2b2b2b;
    --card-dark-glow: #3d3d3d;
    --card-light: #f1f1f1;
    --ink: #2e2e2e;
    --silver: #aaaaaa;
  }
  * { margin: 0; padding: 0; box-sizing: border-box; }
  html, body { width: 1200px; height: 576px; overflow: hidden; }
  body { background: var(--page); position: relative; font-family: "Didact Gothic", sans-serif; }

  .card {
    position: absolute;
    top: 139px;
    height: 292px;
    border-radius: 12px;
    overflow: hidden;
  }
  .card--front {
    left: 82px;
    width: 485px;
    background: radial-gradient(ellipse at 50% 35%, var(--card-dark-glow), var(--card-dark) 70%);
  }
  .card--back {
    left: 602px;
    width: 481px;
    background: var(--card-light);
  }

  .brand {
    position: absolute;
    display: flex;
    align-items: center;
    font-family: "Saira", sans-serif;
    font-weight: 700;
    color: var(--silver);
    line-height: 1;
  }
  .brand__mark { background: var(--silver); display: block; }
  .card--front .brand { left: 88px; top: 100px; gap: 22px; font-size: 84px; }
  .card--front .brand__mark { width: 80px; height: 80px; }
  .card--back .brand { left: 260px; top: 200px; gap: 12px; font-size: 48px; z-index: 2; }
  .card--back .brand__mark { width: 44px; height: 44px; }

  .wave { position: absolute; inset: 0; }

  .holder {
    position: absolute;
    left: 26px; top: 33px;
    font-family: "Saira", sans-serif;
    font-weight: 700;
    font-size: 22px;
    letter-spacing: 1.6px;
    color: var(--ink);
  }
  .contact {
    position: absolute;
    left: 26px; top: 84px;
    list-style: none;
    font-size: 14.5px;
    color: var(--ink);
    line-height: 17px;
  }
  .contact li { display: flex; align-items: center; gap: 9px; }
  .contact svg { width: 10px; height: 10px; fill: var(--ink); }
</style>
</head>
<body>
  <section class="card card--front">
    <div class="brand"><span class="brand__mark"></span>KVTL</div>
  </section>

  <section class="card card--back">
    <svg class="wave" viewBox="0 0 481 292" aria-hidden="true">
      <path d="M0,172 C130,205 280,200 481,70 L481,292 L0,292 Z" fill="var(--card-dark)"/>
      <path d="M0,190 C150,232 310,210 481,98 L481,112 C310,228 150,250 0,212 Z" fill="var(--card-light)"/>
      <path d="M40,184 C170,212 300,196 481,84 L481,90 C300,204 170,218 40,184 Z" fill="var(--card-light)"/>
    </svg>

    <h1 class="holder">VORNAME NAME</h1>
    <ul class="contact">
      <li>Kellberger Str. 18 73418 Rettenau</li>
      <li><svg viewBox="0 0 10 10"><path d="M1,4 Q5,0 9,4 L8,5 L6,4 L6,3 L4,3 L4,4 L2,5 Z M2,6 L8,6 L9,9 L1,9 Z"/></svg>07146-839214-0</li>
      <li><svg viewBox="0 0 10 10"><path d="M0,2 L10,2 L10,8 L0,8 Z M0,2 L5,6 L10,2" stroke="var(--card-light)" stroke-width="0.8"/></svg>name@agentur-kvtl.de</li>
      <li><svg viewBox="0 0 10 10"><circle cx="5" cy="5" r="4.5"/><path d="M0.5,5 H9.5 M5,0.5 V9.5" stroke="var(--card-light)" stroke-width="0.7"/></svg>www.agentur-kvtl.de</li>
    </ul>

    <div class="brand"><span class="brand__mark"></span>KVTL</div>
  </section>
</body>
</html>
```